Shop Window Desgin

I have a big glass window (office), 280cm wide by 302cm high and I want designing an advert for our property management business.

Our main colours are in the proeprty management logo attached. I have also uploaded a photo of the shop front (left window), please take into consideration the door.

I want the following text items placed:

PROPERTY MANAGEMENT
HOLIDAY RENTALS
KEYHOLDING
MARKETING & RESERVATIONS
GARDEN & POOL MAINTENACE
CLEANING & LAUNDRY

```html
<!DOCTYPE html>
<html lang="en">
<head>
<meta charset="utf-8">
<title>Property Services Window Advert</title>
<link rel="stylesheet" href="https://fonts.googleapis.com/css2?family=Bebas+Neue&display=swap">
<style>
  :root {
    --backdrop: #dcdddf;
    --brand-orange: #e87f24;
    --orange-shade: #d26c17;
    --divider: #f6d3b2;
    --white: #ffffff;
    --icon-ink: #5f5f62;
    --street-top: #e08a45;
    --street-bottom: #f3f3f3;
  }
  html, body {
    margin: 0;
    width: 1200px;
    height: 1091px;
    overflow: hidden;
    background: var(--backdrop);
  }
  .window-advert {
    position: absolute;
    left: 91px;
    top: 0;
    width: 1018px;
    height: 1091px;
    display: block;
  }
  .panel-bg { fill: var(--brand-orange); }
  .divider {
    stroke: var(--divider);
    stroke-width: 1.5;
    stroke-dasharray: 7 5;
    fill: none;
  }
  .badge-shadow { fill: var(--orange-shade); }
  .badge { fill: var(--white); }
  .icon {
    fill: none;
    stroke: var(--icon-ink);
    stroke-width: 3;
    stroke-linecap: round;
    stroke-linejoin: round;
  }
  .service-label {
    font-family: "Bebas Neue", "Oswald", sans-serif;
    font-size: 60px;
    fill: var(--white);
    text-anchor: middle;
    letter-spacing: 0.5px;
  }
</style>
</head>
<body>
<svg class="window-advert" viewBox="0 0 1104 1183" xmlns="http://www.w3.org/2000/svg">
  <defs>
    <linearGradient id="street-fill" x1="0" y1="0" x2="0" y2="1">
      <stop offset="0" stop-color="var(--street-top)"/>
      <stop offset="0.78" stop-color="#c9683a"/>
      <stop offset="0.8" stop-color="var(--street-bottom)"/>
      <stop offset="1" stop-color="var(--street-bottom)"/>
    </linearGradient>
  </defs>

  <rect class="panel-bg" x="0" y="0" width="1104" height="1183"/>

  <!-- grid dividers -->
  <line class="divider" x1="576" y1="68" x2="576" y2="925"/>
  <line class="divider" x1="110" y1="317" x2="991" y2="317"/>
  <line class="divider" x1="110" y1="605" x2="991" y2="605"/>

  <!-- service: property management -->
  <g class="service">
    <circle class="badge-shadow" cx="304" cy="130" r="63"/>
    <circle class="badge" cx="299" cy="125" r="62"/>
    <g class="icon">
      <path d="M266 155 h10 v-22 h-10 z"/>
      <path d="M276 137 h22 q8 0 8 6 h-20 M276 153 h30 l30 -18 q4 -6 -4 -6 l-20 10"/>
      <path d="M290 122 v-30 h18 v30"/>
      <path d="M308 122 v-18 l10 -8 l10 8 v18"/>
    </g>
    <text class="service-label" x="299" y="275">PROPERTY MANAGEMENT</text>
  </g>

  <!-- service: holiday rentals -->
  <g class="service">
    <circle class="badge-shadow" cx="812" cy="130" r="63"/>
    <circle class="badge" cx="807" cy="125" r="62"/>
    <g class="icon">
      <path d="M790 160 q4 -30 0 -60"/>
      <path d="M790 100 q-18 -8 -22 6 M790 100 q16 -12 24 2 M790 100 q-6 -14 8 -16"/>
      <circle cx="826" cy="134" r="9"/>
      <path d="M808 150 h36 M816 157 h22 M776 162 h22"/>
    </g>
    <text class="service-label" x="807" y="275">HOLIDAY RENTALS</text>
  </g>

  <!-- service: cleaning & laundry -->
  <g class="service">
    <circle class="badge-shadow" cx="304" cy="418" r="63"/>
    <circle class="badge" cx="299" cy="413" r="62"/>
    <g class="icon">
      <path d="M306 398 h36 l-4 38 h-28 z"/>
      <path d="M290 385 v45 M276 430 h28 v14 h-28 z"/>
      <circle cx="316" cy="392" r="4"/><circle cx="328" cy="390" r="5"/><circle cx="272" cy="400" r="3"/>
    </g>
    <text class="service-label" x="299" y="563">CLEANING &amp; LAUNDRY</text>
  </g>

  <!-- service: keyholding -->
  <g class="service">
    <circle class="badge-shadow" cx="812" cy="418" r="63"/>
    <circle class="badge" cx="807" cy="413" r="62"/>
    <g class="icon">
      <circle cx="830" cy="396" r="9"/>
      <path d="M821 396 h-38 v8 M793 396 v6"/>
      <path d="M772 424 q14 -8 26 2 h16 M774 440 q14 4 30 2 l34 -20"/>
    </g>
    <text class="service-label" x="807" y="563">KEYHOLDING</text>
  </g>

  <!-- service: garden & pool maintenance -->
  <g class="service">
    <circle class="badge-shadow" cx="304" cy="707" r="63"/>
    <circle class="badge" cx="299" cy="702" r="62"/>
    <g class="icon">
      <path d="M292 706 v-30 q0 -6 6 -6 M312 706 v-30 q0 -6 6 -6"/>
      <path d="M292 684 h20 M292 696 h20"/>
      <path d="M268 714 q8 -6 16 0 t16 0 t16 0 t16 0"/>
      <path d="M268 726 q8 -6 16 0 t16 0 t16 0 t16 0"/>
    </g>
    <text class="service-label" x="299" y="852">GARDEN &amp; POOL</text>
    <text class="service-label" x="299" y="919">MAINTENACE</text>
  </g>

  <!-- service: marketing & reservations -->
  <g class="service">
    <circle class="badge-shadow" cx="812" cy="707" r="63"/>
    <circle class="badge" cx="807" cy="702" r="62"/>
    <g class="icon">
      <rect x="788" y="668" width="34" height="62" rx="5"/>
      <circle cx="782" cy="684" r="11"/>
      <path d="M777 684 l4 4 l7 -8"/>
      <path d="M818 748 v-20 l-4 -14 q4 -4 8 2 l4 10 v-12 q6 -2 6 4 v30"/>
    </g>
    <text class="service-label" x="807" y="852">MARKETING &amp;</text>
    <text class="service-label" x="807" y="919">RESERVATIONS</text>
  </g>

  <!-- street of houses -->
  <rect x="0" y="995" width="1104" height="188" fill="url(#street-fill)" role="img" aria-label="Illustrated row of orange houses, townhouses and small trees along a white street"/>
</svg>
</body>
</html>
```